Ashmoor Web Design Project

I need the front page and an internal page designed for this client's website. The logo is attached. Obviously the colors have to go with and/or work with the logo colors. I also attached a very rough brochure layout to help you see the direction we're going in with print materials. The rough site map is also attached. I see a slider on the homepage, the art for which I may come back to you to create. This clinic is in a very high end Dallas neighborhood. The hook is that it's a primary care and urgent facility with convenient hours.

I don't know how much this impacts your design, but this will be a Wordpress site and I'm using a framework called Brovila (brovila.com). If Brovila proves to be inflexible, I'll have to get a template that allows me to execute your design.

This site (http://lanternvaleclinic.com) has the type and quality of content I will eventually have on the Ashmoor site.

I just revised the brief for this project. I added the site map and added details to the overview and the "Must Have" section. Thank you for revisiting the brief. 

Reason: Christmas was a bad time to end it.

Target Market(s)

Women 25-54 with children living at home, income over $150k/year

Industry/Entity Type

Clinic

Requirements
Must have
• Masthead incorporating the logo
Followed by the primary nav
Slider on the home page below that
Dual nav - 1 with the nav in the attached site map
2 secondary nav with areas of healthcare
There will three blocks under the nav
1. It's about time (with a small blurb less than 50 words.
2. It's about choices (with small blurb)
3. It's about you (with small blurb)
Three footer blocks
patient check in link on every page
"No appointment? No problem" icon on every page

```html
<!DOCTYPE html>
<html lang="en">
<head>
<meta charset="utf-8">
<title>Ashmoor Medical</title>
<link href="https://fonts.googleapis.com/css2?family=Open+Sans:wght@400;600;700&family=Oswald:wght@500;600&display=swap" rel="stylesheet">
<style>
:root{
  --green:#1aad55;
  --nav-blue:#0d5c9e;
  --band-blue:#2a4f9a;
  --navy:#1d2f6b;
  --footer:#003b63;
  --red:#e4003a;
  --grey-bg:#ececec;
  --text:#333;
  --white:#fff;
}
*{margin:0;padding:0;box-sizing:border-box}
html,body{width:1047px;height:1200px;overflow:hidden;background:var(--white)}
body{font-family:"Open Sans",Arial,sans-serif;color:var(--text);position:relative}
.abs{position:absolute}
.topbar{left:0;top:0;width:1047px;height:32px;background:var(--green)}
.social{top:3px;width:26px;height:26px;border-radius:4px;background:var(--white);opacity:.9}
.header{left:0;top:32px;width:1047px;height:100px;background:var(--white)}
.brand-mark{left:158px;top:55px;width:52px;height:52px;border-radius:50%;background:var(--nav-blue)}
.brand-name{left:220px;top:60px;font-size:32px;font-weight:700;color:var(--nav-blue);letter-spacing:-.8px;line-height:1}
.brand-tag{left:254px;top:95px;font-size:11px;font-weight:600;color:#333}
.tag-line{top:102px;height:1px;width:30px;background:#333}
.stamp{top:42px;width:84px;height:84px;border-radius:50%;border:3px solid #c9c9c9;display:flex;align-items:center;justify-content:center;text-align:center;font-family:"Oswald",sans-serif;color:#9a9a9a;line-height:1.1;transform:rotate(-8deg)}
.stamp::after{content:"";position:absolute;inset:5px;border:1px solid #d4d4d4;border-radius:50%}
.stamp b{display:block;font-size:17px}
.stamp span{font-size:10px}
.account{top:70px;font-size:11px;color:#555}
.mainnav{left:0;top:132px;width:1047px;height:32px;background:var(--nav-blue);border-bottom:1px solid #8fb3d6}
.mainnav li{list-style:none;position:absolute;top:9px;font-size:10.5px;font-weight:700;color:var(--white);letter-spacing:.2px;white-space:nowrap}
.band{left:0;top:165px;width:1047px;height:263px;background:var(--band-blue)}
.slide{left:155px;top:164px;width:737px;height:264px;border:2px solid #3ec66a;background:linear-gradient(135deg,#6f9a45,#4a7a2c 45%,#8fae5c)}
.dropdown{left:288px;top:166px;width:150px;height:176px;background:rgba(20,50,100,.78)}
.dropdown li{list-style:none;font-size:9.5px;color:var(--white);height:25.6px;padding:3px 0 0 12px;margin:0 6px;border-bottom:1px dashed rgba(255,255,255,.4);position:relative;white-space:nowrap}
.dropdown li::before{content:"";position:absolute;left:0;top:6px;width:5px;height:5px;border-right:2px solid var(--red);border-top:2px solid var(--red);transform:rotate(45deg)}
.slide-copy{left:571px;top:186px;width:274px;height:202px;background:rgba(30,150,70,.82);border:1px solid #bfe6c8;padding:24px 0 0 13px;color:var(--white);font-size:14.6px;line-height:22.5px;letter-spacing:-.45px;white-space:nowrap}
.btn-learn{left:734px;top:346px;width:96px;height:22px;background:linear-gradient(#2b5fc0,#14399b);border:1px solid #9cb4e4;border-radius:3px;color:var(--white);font-size:10px;text-align:center;line-height:20px}
.pager{top:408px;width:11px;height:11px;background:#555;border:1px solid #ddd;color:#eee;font-size:8px;text-align:center;line-height:9px}
.pager.on{background:#fff;color:#333}
.main{left:155px;top:428px;width:737px;height:462px;background:var(--grey-bg)}
.sidebar{left:155px;top:428px;width:197px;height:462px;background:var(--white)}
.sidenav{left:180px;top:442px;width:158px;list-style:none}
.sidenav li{font-family:"Oswald",sans-serif;font-weight:500;font-size:12px;color:var(--navy);height:25.6px;padding:1px 0 0 11px;border-bottom:1px dashed #bbb;position:relative;text-transform:uppercase;white-space:nowrap}
.sidenav li::before{content:"";position:absolute;left:0;top:6px;width:5px;height:5px;border-right:2px solid var(--red);border-top:2px solid var(--red);transform:rotate(45deg)}
.appt{left:170px;top:650px;width:168px;height:208px;background:#e6e6e6;border:1px solid #d0d0d0;border-radius:4px}
.appt-title{left:186px;top:648px;width:136px;height:44px;background:linear-gradient(#d9d9d9,#8c8c8c);border-radius:3px 3px 30px 30px / 3px 3px 12px 12px;border-top:4px solid #555;text-align:center;font-family:"Oswald",sans-serif;font-weight:600;color:var(--white);font-size:13px;line-height:14px;padding-top:7px}
.field{left:182px;width:142px;height:16px;background:var(--white);border:1px solid #ccc;border-radius:2px;font-size:7px;color:#555;padding:2px 7px}
.send{left:194px;top:824px;width:118px;height:24px;background:linear-gradient(#c8c8c8,#777);border-radius:3px;color:var(--white);font-size:11px;text-align:center;line-height:24px}
.welcome{left:378px;top:449px;font-size:17px;font-weight:400;line-height:21px;color:#222;letter-spacing:.4px}
.intro{left:375px;top:497px;width:262px;font-size:10.5px;line-height:14.6px;color:#333}
.more{left:580px;top:579px;font-size:8px;font-weight:700;color:var(--red)}
.video{left:651px;top:446px;width:224px;height:140px;border:6px solid #888;background:linear-gradient(160deg,#b9c4cf,#d9dfe5);box-shadow:0 3px 5px rgba(0,0,0,.3)}
.play{left:741px;top:496px;width:52px;height:38px;border-radius:6px;background:rgba(30,30,30,.8)}
.card{top:616px;width:160px;height:268px;background:var(--white);border:1px solid #ddd}
.card-photo{height:122px;background:linear-gradient(135deg,#9cc070,#c7a07c 55%,#6f9a45)}
.card-label{height:22px;background:linear-gradient(#46c071,#2a9450);color:var(--white);font-family:"Oswald",sans-serif;font-weight:500;font-size:13px;text-align:center;line-height:22px}
.card p{padding:12px 8px 0;font-size:10px;line-height:13.8px;text-align:justify;color:#333}
.footer{left:0;top:890px;width:1047px;height:310px;background:var(--footer);color:var(--white)}
.ftitle{top:900px;font-size:16px;font-weight:400;color:var(--white)}
.sitemap{left:170px;top:925px;list-style:none;font-size:10.5px;line-height:14.7px;color:#dfe7ef;letter-spacing:.3px}
.map{left:375px;top:927px;width:223px;height:190px;background:linear-gradient(135deg,#e9e4d8,#f3efe6 60%,#e7d9a8)}
.contact{left:678px;top:922px;font-size:10.5px;line-height:21.7px;color:#dfe7ef;letter-spacing:.3px}
.rule{left:0;top:1168px;width:1047px;height:1px;background:#5a7c98}
.copy{left:0;top:1178px;width:1047px;text-align:center;font-size:8px;color:#c8d6e2}
</style>
</head>
<body>
<div class="abs topbar"></div>
<div class="abs social" style="left:786px"></div>
<div class="abs social" style="left:821px"></div>
<div class="abs social" style="left:855px"></div>

<header class="abs header"></header>
<div class="abs brand-mark"></div>
<div class="abs brand-name">AshmoorMedical</div>
<div class="abs tag-line" style="left:220px"></div>
<div class="abs brand-tag">Immediate Family and Personal Care</div>
<div class="abs tag-line" style="left:465px"></div>
<div class="abs stamp" style="left:548px"><div><b>NO</b><span>APPOINTMENT</span></div></div>
<div class="abs stamp" style="left:642px;transform:rotate(8deg)"><div><b>NO</b><span>PROBLEM</span></div></div>
<div class="abs account" style="left:766px">Register</div>
<div class="abs account" style="left:818px">Log In</div>
<div class="abs account" style="left:860px">Blog</div>

<nav class="abs mainnav">
  <ul>
    <li style="left:166px">HOME</li><li style="left:223px">ABOUT US</li><li style="left:298px">SERVICES</li><li style="left:370px">STAFF</li><li style="left:423px">INSURANCE</li><li style="left:505px">VIDEOS</li><li style="left:567px">CONTACT US</li>
  </ul>
</nav>

<div class="abs band"></div>
<div class="abs slide" role="img" aria-label="Slider photo of a family outdoors"></div>
<ul class="abs dropdown">
  <li>Immediate Care</li><li>Allergies</li><li>Primary Care</li><li>Women's Health</li><li>Medical Spa Treatments</li><li>Men's Health</li><li>Weight Loss</li>
</ul>
<svg class="abs" style="left:163px;top:279px" width="30" height="36" viewBox="0 0 30 36"><polyline points="24,3 8,18 24,33" fill="none" stroke="#fff" stroke-width="6"/></svg>
<svg class="abs" style="left:853px;top:279px" width="30" height="36" viewBox="0 0 30 36"><polyline points="6,3 22,18 6,33" fill="none" stroke="#fff" stroke-width="6"/></svg>
<div class="abs slide-copy">Lorem ipsum dolor sit amet consec-<br>tetuer adipiscing elit. Nam cursus.<br>Morbi ut mi. Lorem ipsum dolor sit<br>amet consectetuer adipiscing elit.<br>Nam cursus. Morbi ut mi.</div>
<div class="abs btn-learn">Learn more</div>
<div class="abs pager" style="left:815px">1</div>
<div class="abs pager on" style="left:830px">2</div>
<div class="abs pager" style="left:845px">3</div>
<div class="abs pager" style="left:860px">4</div>

<main class="abs main"></main>
<aside class="abs sidebar"></aside>
<ul class="abs sidenav">
  <li>Immediate Care</li><li>Allergies</li><li>Primary Care</li><li>Women's Health</li><li>Medical Spa Treatments</li><li>Men's Health</li><li>Weight Loss</li>
</ul>
<div class="abs appt"></div>
<div class="abs appt-title">APPOINTMENT<br>REQUEST</div>
<div class="abs field" style="top:702px">Name</div>
<div class="abs field" style="top:722px">Email</div>
<div class="abs field" style="top:742px">Subject</div>
<div class="abs field" style="top:761px;height:55px">Message</div>
<div class="abs send">Send</div>

<h1 class="abs welcome">Welcome to<br>AshmoorFamilyMedical</h1>
<p class="abs intro">Lorem ipsum dolor sit amet, consectetuer adipiscing elit. Nam cursus. Morbi ut mi. Nullam enim leo, egestas id, condimentum at, laoreet mattis, massa. Sed eleifend nonummy diam. Praesent mauris ante, elementum et, bibendum at, posuere sit amet, nibh.</p>
<div class="abs more">Learn more &#8250;</div>
<div class="abs video" role="img" aria-label="Clinic introduction video"></div>
<svg class="abs play" viewBox="0 0 52 38"><polygon points="20,10 20,28 34,19" fill="#fff"/></svg>

<section class="abs card" style="left:375px">
  <div class="card-photo" role="img" aria-label="Photo of a smiling family"></div>
  <div class="card-label">IT'S ABOUT TIME</div>
  <p>Lorem ipsum dolor sit amet consectetuer adipiscing elit. Nam cursus. Morbi ut mi Nullam enim leo, egestas id condimentum at, laoreet mattis, massa. Sed eleifend nonummy diam. Praesent</p>
</section>
<section class="abs card" style="left:547px">
  <div class="card-photo" role="img" aria-label="Photo of a mother hugging her daughter"></div>
  <div class="card-label">IT'S ABOUT CHOICES</div>
  <p>Lorem ipsum dolor sit amet consectetuer adipiscing elit. Nam cursus. Morbi ut mi Nullam enim leo, egestas id condimentum at, laoreet mattis, massa. Sed eleifend nonummy diam. Praesent</p>
</section>
<section class="abs card" style="left:719px">
  <div class="card-photo" role="img" aria-label="Photo of a smiling couple"></div>
  <div class="card-label">IT'S ABOUT YOU</div>
  <p>Lorem ipsum dolor sit amet consectetuer adipiscing elit. Nam cursus. Morbi ut mi Nullam enim leo, egestas id condimentum at, laoreet mattis, massa. Sed eleifend nonummy diam. Praesent</p>
</section>

<footer class="abs footer"></footer>
<h2 class="abs ftitle" style="left:166px">Sitemap</h2>
<ul class="abs sitemap">
  <li>Home</li><li>About Us</li><li>Services</li><li>Staff</li><li>Insurance</li><li>Videos</li><li>Immediate Care</li><li>Allergies</li><li>Primary Care</li><li>Women's Health</li><li>Medical Spa Treatments</li><li>Men's Health</li><li>Weight Loss</li><li>Contact Us</li>
</ul>
<h2 class="abs ftitle" style="left:375px">Location</h2>
<div class="abs map" role="img" aria-label="Street map showing the clinic location"></div>
<h2 class="abs ftitle" style="left:677px">Contact Us</h2>
<div class="abs contact">AshmoorFamilyMedical<br>4420 Ashmoor Ave (at Elm Pkwy) Ste<br>210, Dallas, TX 75290<br><br>Tel: (555) 014 2020<br>Fax: (555) 014 2020<br>E-mail: info@ashmoorfamilymedical.com</div>
<div class="abs rule"></div>
<div class="abs copy">Copyright 2012 AshmoorFamilyMedical. All rights reserved.</div>
</body>
</html>
```